brovlanepass.net

Develop a website for brolanepass.net will be a site to sell tickets for concerts, shows, shows, theaters and others. I need a web design easy view, very easy to use and accumulate events by date. The aim is to develop the site was connected to a complex system that is already developed. (Important this page to a robust system was connected via links the idea is to develop only the front view)
Updates

Reason: I need more designs yet we have not made the decision

Target Market(s)

millennials, adults, who want to enjoy concerts and shows

Industry/Entity Type

Event

Number of Pages Required

5+ page

Colors
1b1b1b
aaaaaa
ffffff

Requirements
Must have
• Easy Vista, accumulation of upcoming events, past events. The tabs should have are: 1 Start: In this part of upcoming events occur. You could put a banner on the top and down the events by date. 2. How to order: page with instructions on how to purchase tickets 3. About Us: The company history 4. Contact: Phones and template for contact by mail 5. Our policies: shopping 6. Notice Privacy: Privacy Notice Copoy 7. Centers Sale: physical places where they can purchase tickets Promoters 8. access: Link to a template
Nice to have
• as you can see p www.quimbarostage.net or farunda.net or farunda.org or gallowmerk.net (important this page to a robust system was connected via links the idea is to develop only the front view)
Should not have
• Many things Tangled

```html
<!DOCTYPE html>
<html lang="en">
<head>
<meta charset="utf-8">
<title>Brovlane Pass — Tickets for concerts, shows and theaters</title>
<link rel="stylesheet" href="https://fonts.googleapis.com/css2?family=Montserrat:wght@400;500;600;700&family=Open+Sans:wght@400;600;700&family=Fira+Sans+Extra+Condensed:wght@600;700&display=swap">
<style>
:root{
  --ink:#1b1b1b;
  --grey:#aaaaaa;
  --white:#ffffff;
  --soft:#f3f3f3;
  --line:#dddddd;
  --text:#444444;
  --muted:#8a8a8a;
  --field:#eeeeee;
}
*{box-sizing:border-box;margin:0;padding:0}
html,body{width:1200px;height:2539px;overflow:hidden;background:var(--white)}
body{position:relative;font-family:"Open Sans",Arial,sans-serif;color:var(--ink)}
a{color:inherit;text-decoration:none}
.container{position:absolute;left:75px;width:1050px}

/* header */
.site-header{position:absolute;top:0;left:0;width:1200px;height:83px}
.brand{position:absolute;left:76px;top:26px;font-family:"Montserrat",sans-serif;font-weight:700;font-size:25px;letter-spacing:.5px;color:var(--ink)}
.search{position:absolute;left:379px;top:22px;width:362px;height:41px;display:flex}
.search-field{flex:1;background:var(--field);font-size:12px;color:#666;padding:12px 12px}
.search-btn{width:54px;background:var(--grey);display:flex;align-items:center;justify-content:center}
.social{position:absolute;left:786px;top:32px;display:flex;gap:18px}
.social span{width:17px;height:17px;border-radius:50%;background:#9a9a9a;display:block}
.cart{position:absolute;left:1020px;top:22px;display:flex;align-items:center;gap:14px;font-family:"Montserrat",sans-serif;font-size:12px;font-weight:500}
.cart-icon{width:37px;height:37px;border:1.5px solid var(--ink);border-radius:50%;display:flex;align-items:center;justify-content:center}

/* nav */
.main-nav{position:absolute;top:83px;left:0;width:1200px;height:56px;background:var(--ink)}
.main-nav ul{list-style:none;position:absolute;left:75px;top:0;height:56px;display:flex;align-items:center;gap:41px}
.main-nav li{font-family:"Montserrat",sans-serif;font-size:12px;font-weight:500;color:var(--white)}
.nav-access{position:absolute;left:1000px;top:0;width:125px;height:56px;background:var(--grey);color:var(--ink);display:flex;align-items:center;justify-content:center;gap:7px;font-family:"Montserrat",sans-serif;font-size:12px;font-weight:500}

/* hero */
.hero{top:154px;height:508px;background:linear-gradient(180deg,#6d6a62 0%,#c9a56a 40%,#e8c58a 55%,#3a3631 100%)}
.hero-caption{position:absolute;left:0;top:284px;width:485px;height:224px;background:rgba(27,27,27,.78);padding:26px 30px}
.hero-title{font-family:"Fira Sans Extra Condensed",sans-serif;font-weight:700;font-size:40px;line-height:44px;color:var(--white);letter-spacing:.5px;white-space:nowrap}
.hero-text{margin-top:12px;font-size:18px;font-weight:600;color:var(--white);line-height:27px}
.btn-dark{margin-top:14px;width:174px;height:49px;background:var(--ink);color:var(--white);font-family:"Montserrat",sans-serif;font-weight:700;font-size:16px;display:flex;align-items:center;justify-content:center}
.hero-dots{position:absolute;right:42px;top:462px;display:flex;gap:10px}
.hero-dots span{width:11px;height:11px;border-radius:50%;background:var(--white)}
.hero-dots span.active{background:var(--ink)}

/* featured */
.section-title{position:absolute;left:0;width:1200px;text-align:center;font-family:"Montserrat",sans-serif;font-weight:700;font-size:23px;letter-spacing:.6px;color:var(--ink)}
.featured-grid{top:770px;height:262px}
.ticket-card{position:absolute;top:0;width:240px;height:262px}
.ticket-card .photo{position:absolute;inset:0}
.ticket-card .overlay{position:absolute;left:0;bottom:0;width:100%;height:93px;background:rgba(27,27,27,.88);text-align:center}
.ticket-card h3{margin-top:14px;font-family:"Montserrat",sans-serif;font-weight:700;font-size:14px;color:var(--white)}
.btn-outline-sm{display:inline-block;margin-top:10px;width:108px;height:33px;line-height:29px;border:2px solid var(--white);font-family:"Montserrat",sans-serif;font-weight:700;font-size:10px;color:var(--white)}

/* events */
.events{position:absolute;top:1085px;left:0;width:1200px;height:865px;background:var(--soft)}
.event-grid{top:115px;height:581px}
.event{position:absolute;width:349px;height:290px;overflow:hidden}
.event .photo{position:absolute;inset:0}
.event .shade{position:absolute;left:0;bottom:0;width:100%;height:110px;background:linear-gradient(180deg,rgba(0,0,0,0),rgba(0,0,0,.65))}
.event-date{position:absolute;left:0;bottom:0;width:85px;height:110px;background:rgba(255,255,255,.94);padding-top:16px;text-align:center;font-family:"Montserrat",sans-serif}
.event-date .day{font-size:30px;font-weight:700;line-height:1}
.event-date .month{font-size:12px;font-weight:700;margin-top:8px}
.event-date .time{font-size:12px;color:var(--muted);margin-top:8px}
.event-info{position:absolute;left:150px;bottom:16px;width:180px;font-family:"Montserrat",sans-serif;color:var(--white)}
.event-info h3{font-size:15px;font-weight:700;padding-bottom:8px;border-bottom:1px solid rgba(255,255,255,.8);white-space:nowrap}
.event-info p{margin-top:8px;font-family:"Open Sans",sans-serif;font-size:12.5px;font-weight:600;display:flex;align-items:center;gap:7px}
.btn-outline{position:absolute;left:479px;top:758px;width:242px;height:54px;border:2px solid #9a9a9a;background:var(--white);display:flex;align-items:center;justify-content:center;font-family:"Montserrat",sans-serif;font-weight:700;font-size:14px}

/* info */
.info{position:absolute;top:1950px;left:0;width:1200px;height:440px}
.info-col{position:absolute;top:56px;width:360px;text-align:center}
.info-icon{width:122px;height:122px;margin:0 auto;border:2px solid #c7c7c7;border-radius:50%;display:flex;align-items:center;justify-content:center}
.info-col h2{margin-top:26px;font-family:"Montserrat",sans-serif;font-weight:700;font-size:20px;letter-spacing:.4px}
.info-col p{margin:10px auto 0;width:272px;font-size:13.5px;line-height:1.6;color:var(--text)}
.btn-read{display:inline-block;margin-top:30px;width:108px;height:33px;line-height:29px;border:2px solid #9a9a9a;font-family:"Montserrat",sans-serif;font-weight:700;font-size:11px;color:#555}
.divider{position:absolute;top:56px;width:1px;height:306px;background:var(--line)}

/* footer */
.site-footer{position:absolute;top:2390px;left:0;width:1200px;height:149px;background:var(--ink);color:var(--white)}
.footer-nav{position:absolute;left:77px;top:38px;display:flex;gap:23px;list-style:none;font-size:13px;color:#d0d0d0}
.copyright{position:absolute;left:77px;top:81px;font-size:11.5px;line-height:1.8;color:#9a9a9a}
.newsletter{position:absolute;left:883px;top:36px;width:242px}
.newsletter h4{font-family:"Montserrat",sans-serif;font-size:12px;font-weight:600;letter-spacing:.3px}
.newsletter-form{margin-top:15px;display:flex;height:34px}
.newsletter-field{flex:1;background:#7a7a7a;font-size:11.5px;font-style:italic;color:#cfcfcf;padding:9px 11px}
.newsletter-btn{width:42px;background:var(--white);display:flex;align-items:center;justify-content:center}
</style>
</head>
<body>

<header class="site-header">
  <a class="brand" href="#">BROVLANE PASS</a>
  <form class="search">
    <div class="search-field">Search concert, shows...</div>
    <div class="search-btn">
      <svg width="18" height="18" viewBox="0 0 18 18"><circle cx="7.5" cy="7.5" r="5.5" fill="none" stroke="#fff" stroke-width="2.2"/><line x1="11.5" y1="11.5" x2="16" y2="16" stroke="#fff" stroke-width="2.4" stroke-linecap="round"/></svg>
    </div>
  </form>
  <div class="social" aria-label="Social links"><span></span><span></span><span></span><span></span><span></span><span></span></div>
  <a class="cart" href="#">
    <span class="cart-icon"><svg width="16" height="14" viewBox="0 0 16 14"><path d="M1 1h2.5l2 8h7.5l1.5-6H4.5" fill="none" stroke="#1b1b1b" stroke-width="1.6" stroke-linejoin="round"/><circle cx="6.5" cy="12" r="1.3" fill="#1b1b1b"/><circle cx="12" cy="12" r="1.3" fill="#1b1b1b"/></svg></span>
    <span>CART <b>(0)</b></span>
  </a>
</header>

<nav class="main-nav">
  <ul>
    <li>HOME</li><li>HOW TO ORDER</li><li>ABOUT US</li><li>CONTACT US</li><li>POLICIES</li><li>PRIVACY</li><li>CENTER SALE</li>
  </ul>
  <a class="nav-access" href="#"><svg width="10" height="12" viewBox="0 0 10 12"><rect x="1" y="5" width="8" height="7" fill="#1b1b1b"/><path d="M2.8 5V3.5a2.2 2.2 0 0 1 4.4 0V5" fill="none" stroke="#1b1b1b" stroke-width="1.4"/></svg>ACCESS</a>
</nav>

<section class="container hero">
  <div class="photo" role="img" aria-label="Band of four musicians with guitars posing against a sunset sky" style="position:absolute;inset:0"></div>
  <div class="hero-caption">
    <h1 class="hero-title">CONSECTETUER ADIPISCING</h1>
    <p class="hero-text">Lorem ipsum dolor sit amet, consect- etuer<br>adipiscing elit, sed diam nonummy..</p>
    <a class="btn-dark" href="#">BUY TICKETS</a>
  </div>
  <div class="hero-dots"><span class="active"></span><span></span><span></span><span></span></div>
</section>

<h2 class="section-title" style="top:710px">FEATURED TICKETS FOR SELL</h2>
<section class="container featured-grid">
  <article class="ticket-card" style="left:1px">
    <div class="photo" role="img" aria-label="Musician playing guitar on stage" style="background:linear-gradient(135deg,#3a2a22,#8a6a50 60%,#d9d2c8)"></div>
    <div class="overlay"><h3>CONCERTS</h3><a class="btn-outline-sm" href="#">BUY TICKETS</a></div>
  </article>
  <article class="ticket-card" style="left:269px">
    <div class="photo" role="img" aria-label="Fashion show runway with models" style="background:linear-gradient(180deg,#6a6a6a,#2a2a2a)"></div>
    <div class="overlay"><h3>SHOWS</h3><a class="btn-outline-sm" href="#">BUY TICKETS</a></div>
  </article>
  <article class="ticket-card" style="left:539px">
    <div class="photo" role="img" aria-label="Acrobat performing in a theater under blue lights" style="background:linear-gradient(180deg,#1d2b55,#4a5a8a 60%,#2a2a3a)"></div>
    <div class="overlay"><h3>THEATERS</h3><a class="btn-outline-sm" href="#">BUY TICKETS</a></div>
  </article>
  <article class="ticket-card" style="left:809px">
    <div class="photo" role="img" aria-label="Cinema audience watching a film" style="background:linear-gradient(135deg,#b8402e,#d98a60 50%,#e9d0b8)"></div>
    <div class="overlay"><h3>OTHERS</h3><a class="btn-outline-sm" href="#">BUY TICKETS</a></div>
  </article>
</section>

<section class="events">
  <h2 class="section-title" style="top:54px">UPCOMING EVENTS</h2>
  <div class="container event-grid">
    <article class="event" style="left:0;top:0">
      <div class="photo" role="img" aria-label="Rock band performing on a smoky stage" style="background:linear-gradient(135deg,#2a2622,#6a5a48 55%,#1b1b1b)"></div>
      <div class="shade"></div>
      <div class="event-date"><div class="day">18</div><div class="month">MAR 2017</div><div class="time">12:30</div></div>
      <div class="event-info"><h3>LOREM IPSUM DOLOR</h3><p><svg width="8" height="11" viewBox="0 0 8 11"><path d="M4 0a4 4 0 0 0-4 4c0 3 4 7 4 7s4-4 4-7a4 4 0 0 0-4-4z" fill="#fff"/><circle cx="4" cy="4" r="1.4" fill="#555"/></svg>Tallow Road,Brennick</p></div>
    </article>
    <article class="event" style="left:350px;top:0">
      <div class="photo" role="img" aria-label="Colourful musical theater cast on stage" style="background:linear-gradient(135deg,#3a2240,#8a4a6a 50%,#2a2a2a)"></div>
      <div class="shade"></div>
      <div class="event-date"><div class="day">18</div><div class="month">MAR 2017</div><div class="time">12:30</div></div>
      <div class="event-info"><h3>LOREM IPSUM DOLOR</h3><p><svg width="8" height="11" viewBox="0 0 8 11"><path d="M4 0a4 4 0 0 0-4 4c0 3 4 7 4 7s4-4 4-7a4 4 0 0 0-4-4z" fill="#fff"/><circle cx="4" cy="4" r="1.4" fill="#555"/></svg>Tallow Road,Brennick</p></div>
    </article>
    <article class="event" style="left:701px;top:0">
      <div class="photo" role="img" aria-label="Masked mime performer against a dark background" style="background:linear-gradient(135deg,#0d0d0d,#4a4a4a 55%,#111)"></div>
      <div class="shade"></div>
      <div class="event-date"><div class="day">18</div><div class="month">MAR 2017</div><div class="time">12:30</div></div>
      <div class="event-info"><h3>LOREM IPSUM DOLOR</h3><p><svg width="8" height="11" viewBox="0 0 8 11"><path d="M4 0a4 4 0 0 0-4 4c0 3 4 7 4 7s4-4 4-7a4 4 0 0 0-4-4z" fill="#fff"/><circle cx="4" cy="4" r="1.4" fill="#555"/></svg>Tallow Road,Brennick</p></div>
    </article>
    <article class="event" style="left:0;top:291px">
      <div class="photo" role="img" aria-label="Exhibition hall with bright blue stage lighting" style="background:linear-gradient(135deg,#0e2a4a,#2a7aa8 50%,#3a1a2a)"></div>
      <div class="shade"></div>
      <div class="event-date"><div class="day">18</div><div class="month">MAR 2017</div><div class="time">12:30</div></div>
      <div class="event-info"><h3>LOREM IPSUM DOLOR</h3><p><svg width="8" height="11" viewBox="0 0 8 11"><path d="M4 0a4 4 0 0 0-4 4c0 3 4 7 4 7s4-4 4-7a4 4 0 0 0-4-4z" fill="#fff"/><circle cx="4" cy="4" r="1.4" fill="#555"/></svg>Tallow Road,Brennick</p></div>
    </article>
    <article class="event" style="left:350px;top:291px">
      <div class="photo" role="img" aria-label="Front of a red vintage car at a car show" style="background:linear-gradient(135deg,#4a5a58,#9a4a3a 45%,#c8b48a)"></div>
      <div class="shade"></div>
      <div class="event-date"><div class="day">18</div><div class="month">MAR 2017</div><div class="time">12:30</div></div>
      <div class="event-info"><h3>LOREM IPSUM DOLOR</h3><p><svg width="8" height="11" viewBox="0 0 8 11"><path d="M4 0a4 4 0 0 0-4 4c0 3 4 7 4 7s4-4 4-7a4 4 0 0 0-4-4z" fill="#fff"/><circle cx="4" cy="4" r="1.4" fill="#555"/></svg>Tallow Road,Brennick</p></div>
    </article>
    <article class="event" style="left:701px;top:291px">
      <div class="photo" role="img" aria-label="Concert crowd facing a stage lit in red and blue" style="background:linear-gradient(180deg,#2a3a6a,#8a2a2a 55%,#3a0e0e)"></div>
      <div class="shade"></div>
      <div class="event-date"><div class="day">18</div><div class="month">MAR 2017</div><div class="time">12:30</div></div>
      <div class="event-info"><h3>LOREM IPSUM DOLOR</h3><p><svg width="8" height="11" viewBox="0 0 8 11"><path d="M4 0a4 4 0 0 0-4 4c0 3 4 7 4 7s4-4 4-7a4 4 0 0 0-4-4z" fill="#fff"/><circle cx="4" cy="4" r="1.4" fill="#555"/></svg>Tallow Road,Brennick</p></div>
    </article>
  </div>
  <a class="btn-outline" href="#">VIEW ALL EVENTS</a>
</section>

<section class="info">
  <div class="info-col" style="left:60px">
    <div class="info-icon"><svg width="54" height="40" viewBox="0 0 54 40" fill="#9a9a9a"><circle cx="27" cy="9" r="8"/><circle cx="11" cy="13" r="6"/><circle cx="43" cy="13" r="6"/><path d="M14 40v-8a13 13 0 0 1 26 0v8z"/><path d="M0 40v-6a10 10 0 0 1 14-9 16 16 0 0 0-3 9v6z"/><path d="M54 40v-6a10 10 0 0 0-14-9 16 16 0 0 1 3 9v6z"/></svg></div>
    <h2>ABOUT US</h2>
    <p>Vestibulum ante ipsum primis in faucibus orci luctus et ultrices posuere cubilia egestas risus in magna varius..</p>
    <a class="btn-read" href="#">READ MORE</a>
  </div>
  <div class="divider" style="left:420px"></div>
  <div class="info-col" style="left:420px">
    <div class="info-icon"><svg width="56" height="38" viewBox="0 0 56 38"><rect x="9" y="2" width="38" height="26" rx="2" fill="none" stroke="#8a8a8a" stroke-width="3"/><path d="M2 32h52l-3 5H5z" fill="#8a8a8a"/></svg></div>
    <h2>HOW TO ORDER</h2>
    <p>Vestibulum ante ipsum primis in faucibus orci luctus et ultrices posuere cubilia egestas risus in magna varius..</p>
    <a class="btn-read" href="#">READ MORE</a>
  </div>
  <div class="divider" style="left:780px"></div>
  <div class="info-col" style="left:780px">
    <div class="info-icon"><svg width="30" height="44" viewBox="0 0 30 44"><path d="M15 0A15 15 0 0 0 0 15c0 11 15 29 15 29s15-18 15-29A15 15 0 0 0 15 0z" fill="#8a8a8a"/><circle cx="15" cy="15" r="5.5" fill="#fff"/></svg></div>
    <h2>CENTER SALE</h2>
    <p>Vestibulum ante ipsum primis in faucibus orci luctus et ultrices posuere cubilia egestas risus in magna varius..</p>
    <a class="btn-read" href="#">READ MORE</a>
  </div>
</section>

<footer class="site-footer">
  <ul class="footer-nav">
    <li>Home</li><li>How to Order</li><li>About us</li><li>Contact Us</li><li>Policies</li><li>Privacy</li><li>Center Sale</li><li>Access</li>
  </ul>
  <p class="copyright">Copyright © 2017, Company Name<br>All Right Reserved</p>
  <div class="newsletter">
    <h4>NEWSLETTER SIGN UP</h4>
    <form class="newsletter-form">
      <div class="newsletter-field">Email Address</div>
      <div class="newsletter-btn"><svg width="16" height="16" viewBox="0 0 16 16"><path d="M1 7.5L15 1l-4 14-3.5-5.5z" fill="#1b1b1b"/><path d="M7.5 9.5L15 1" stroke="#fff" stroke-width="1"/></svg></div>
    </form>
  </div>
</footer>

</body>
</html>
```